****Business Card Design for Quarrystone Development. Design based around attached logo/company name

I’m looking for business card design for my company Quarrystone Development Group,LLC. Design should be professional, sharp and minimal. Outside of the attached logos, greyscale colors for remainder of cards. My thoughts are two-sided card with attached logo on one side and my info on the other but open to one-sided as well with right design.
Target Market(s)
Real estate professionals including banks, private investors, property owners, developers, commercial tenants like Brewlantern, Grovika or Tanquist’s.
Industry/Entity Type
Commercial real estate development and investments.
Contact Information for Business Card
Name, title, email, phone #’s, web address and physical address
Font styles to use
Other font styles liked:
- Helvetica, Garamond, etc
Colors
Designer to choose only greyscale colors for use in the design.
Requirements
Must have
- Attached logo first or second options.
Nice to have
- Two sided card with logo on one side. Attached Logo/company name can be laid out any way that flows as long as it’s legible.name
Should not have
- No loud colors. ***Please do not include logo, I have removed the company design with a logo image.

```html
<!DOCTYPE html>
<html lang="en">
<head>
<meta charset="utf-8">
<title>Quarrystone Development Group, LLC – Business Card</title>
<link href="https://fonts.googleapis.com/css2?family=EB+Garamond:wght@400;700&family=Arimo:wght@400&display=swap" rel="stylesheet">
<style>
  :root {
    --page-bg: #dcdcdc;
    --card-bg: #ffffff;
    --slate: #5d6677;
    --ink-name: #4c5567;
    --ink-body: #7a7d84;
    --stripe-grey: #9a9a9a;
    --mark-tint: #f3f3f3;
  }
  * { margin: 0; padding: 0; box-sizing: border-box; }
  html, body {
    width: 1200px;
    height: 1059px;
    overflow: hidden;
    background: var(--page-bg);
  }
  .card {
    position: absolute;
    left: 222px;
    top: 310px;
    width: 817px;
    height: 431px;
    background: var(--card-bg);
    border-radius: 18px;
    overflow: hidden;
  }
  .card__mark-area {
    position: absolute;
    left: 393px;
    top: 2px;
    width: 326px;
    height: 312px;
    background: radial-gradient(ellipse at 55% 55%, var(--mark-tint) 0%, rgba(243,243,243,0.6) 45%, rgba(255,255,255,0) 72%);
  }
  .card__wave {
    position: absolute;
    left: 0;
    top: 0;
    width: 817px;
    height: 431px;
  }
  .brand {
    position: absolute;
    left: 78px;
    top: 183px;
    width: 290px;
    font-family: "EB Garamond", Garamond, serif;
    font-weight: 400;
    font-size: 27px;
    line-height: 32px;
    color: var(--ink-name);
  }
  .contact {
    position: absolute;
    left: 412px;
    top: 117px;
    font-family: "Arimo", Helvetica, Arial, sans-serif;
    color: var(--ink-body);
    font-size: 17px;
    line-height: 1;
  }
  .contact__name {
    font-family: "EB Garamond", Garamond, serif;
    font-weight: 700;
    font-size: 24px;
    letter-spacing: 0.5px;
    color: var(--ink-name);
    text-transform: uppercase;
  }
  .contact__title { margin-top: 3px; }
  .contact__address { margin-top: 19px; line-height: 22px; }
  .contact__list { list-style: none; margin-top: 13px; }
  .contact__item {
    display: flex;
    align-items: center;
    height: 25.5px;
  }
  .contact__icon {
    width: 13px;
    height: 13px;
    margin-right: 8px;
    fill: var(--ink-name);
    flex: none;
  }
</style>
</head>
<body>
  <div class="card">
    <div class="card__mark-area" role="img" aria-label="Faint brand mark watermark"></div>

    <svg class="card__wave" viewBox="0 0 817 431" aria-hidden="true">
      <path d="M0,331 Q330,452 540,398 Q330,440 0,341 Z" fill="var(--stripe-grey)"/>
      <path d="M0,345 Q330,470 817,320 L817,431 L0,431 Z" fill="var(--slate)"/>
    </svg>

    <p class="brand">Quarrystone Development<br>Group, LLC</p>

    <div class="contact">
      <p class="contact__name">Daniel Verhoek</p>
      <p class="contact__title">Founder/CEO</p>
      <p class="contact__address">8474 Street Address Name<br>Counter name AB 7841</p>
      <ul class="contact__list">
        <li class="contact__item">
          <svg class="contact__icon" viewBox="0 0 16 16"><path d="M3.6 1.2 6 3.6c.4.4.4 1 0 1.4L4.9 6.1a9 9 0 0 0 5 5l1.1-1.1c.4-.4 1-.4 1.4 0l2.4 2.4c.4.4.4 1 0 1.4l-1.3 1.3c-.6.6-1.5.8-2.300.5A15 15 0 0 1 .4 4.8c-.3-.8-.1-1.700.5-2.3L2.2 1.2c.4-.4 1-.4 1.4 0z"/></svg>
          <span>(123)-555-0148</span>
        </li>
        <li class="contact__item">
          <svg class="contact__icon" viewBox="0 0 16 16"><path d="M1 3h14v1.2L8 8.6 1 4.2z"/><path d="M1 5.6l7 4.4 7-4.4V13H1z"/></svg>
          <span>info@quarrystonedevelopment.com</span>
        </li>
        <li class="contact__item">
          <svg class="contact__icon" viewBox="0 0 16 16"><circle cx="8" cy="8" r="7"/><path d="M4 5c1.5 0 2 1 3 1.5S8 8 7 9s-2 .5-2 2M10 3c0 1.5 1 2 2 2M11 9c1 0 2 1 1.5 2.5" stroke="#fff" stroke-width="1.2" fill="none"/></svg>
          <span>www.quarrystonedevelopment.com</span>
        </li>
      </ul>
    </div>
  </div>
</body>
</html>
```